BOLD & MINIMALIST DESIGN NEEDED

We want a very bold but minimalistic business card design that is impactful and utilizes both sides of the business card. Our current logo is included for your use.

We want bold fonts and good use of negative space. We don't want the logo to overpower the design.

Target Market(s)

Professionals who are building new commercial buildings.

Industry/Entity Type

Construction

Contact Information for Business Card

Name, Title, email, office phone, cell phone, website

Font styles to use
Serif
Sans Serif

Requirements
Must have
• Bold design!

```html
<!DOCTYPE html>
<html lang="en">
<head>
<meta charset="utf-8">
<title>Ridgeline Design + Build — Business Card</title>
<link rel="stylesheet" href="https://fonts.googleapis.com/css2?family=Montserrat:wght@400;500;800&display=swap">
<style>
  :root {
    --backdrop: #d4d4d4;
    --card: #f4f4f2;
    --edge-green: #5e9a2c;
    --brand-green: #5b8f2e;
    --ink: #141414;
    --muted: #8a8a8a;
    --rule: #d9d9d6;
  }
  * { box-sizing: border-box; margin: 0; padding: 0; }
  html, body {
    width: 1200px;
    height: 1051px;
    overflow: hidden;
    background: var(--backdrop);
    font-family: "Montserrat", sans-serif;
  }
  .sheet {
    width: 1200px;
    height: 1051px;
    display: flex;
    flex-direction: column;
    align-items: center;
    justify-content: center;
    gap: 60px;
  }
  .card {
    width: 700px;
    height: 400px;
    background: var(--card);
    border-bottom: 8px solid var(--edge-green);
    box-shadow: 0 14px 30px rgba(0,0,0,0.18);
    position: relative;
  }

  /* Contact side */
  .card--contact {
    display: flex;
    align-items: center;
  }
  .identity {
    width: 340px;
    padding-right: 40px;
    text-align: right;
  }
  .identity__name {
    color: var(--brand-green);
    font-weight: 800;
    font-size: 30px;
    letter-spacing: 0.5px;
    text-transform: uppercase;
  }
  .identity__title {
    color: var(--muted);
    font-weight: 400;
    font-size: 20px;
    margin-top: 6px;
  }
  .divider {
    width: 2px;
    height: 120px;
    background: var(--rule);
  }
  .contact-list {
    list-style: none;
    padding-left: 40px;
  }
  .contact-list__item {
    display: flex;
    align-items: center;
    gap: 12px;
    color: var(--muted);
    font-size: 19px;
    line-height: 32px;
  }
  .contact-list__icon {
    width: 16px;
    height: 16px;
    flex: none;
  }

  /* Brand side */
  .card--brand {
    display: flex;
    align-items: center;
    justify-content: center;
  }
  .brand {
    display: flex;
    align-items: center;
    gap: 20px;
  }
  .brand__mark {
    width: 38px;
    height: 38px;
    background: var(--brand-green);
  }
  .brand__name {
    color: var(--ink);
    font-weight: 800;
    font-size: 40px;
    line-height: 1.1;
    letter-spacing: 1px;
    text-transform: uppercase;
  }
</style>
</head>
<body>
<main class="sheet">
  <section class="card card--contact" aria-label="Contact side">
    <div class="identity">
      <p class="identity__name">Marcus Orland</p>
      <p class="identity__title">President</p>
    </div>
    <div class="divider"></div>
    <ul class="contact-list">
      <li class="contact-list__item">
        <svg class="contact-list__icon" viewBox="0 0 16 16" aria-hidden="true"><path fill="#5b8f2e" d="M3.6 1.2l2.3 2.9-1.3 1.7a9 9 0 0 0 5.6 5.6l1.7-1.3 2.9 2.3-1.6 2.2C7.4 14.6 1.4 8.6 1.4 2.8z"/></svg>
        555-014-2200
      </li>
      <li class="contact-list__item">
        <svg class="contact-list__icon" viewBox="0 0 16 16" aria-hidden="true"><rect x="4" y="1" width="8" height="14" rx="1.5" fill="none" stroke="#5b8f2e" stroke-width="1.6"/><circle cx="8" cy="12.3" r="0.9" fill="#5b8f2e"/></svg>
        555-014-2201
      </li>
      <li class="contact-list__item">
        <svg class="contact-list__icon" viewBox="0 0 16 16" aria-hidden="true"><rect x="1" y="3" width="14" height="10" fill="#5b8f2e"/><path d="M1.5 3.5L8 9l6.5-5.5" fill="none" stroke="#f4f4f2" stroke-width="1.3"/></svg>
        m.orland@rdb-build.com
      </li>
      <li class="contact-list__item">
        <svg class="contact-list__icon" viewBox="0 0 16 16" aria-hidden="true"><circle cx="8" cy="8" r="6.5" fill="none" stroke="#5b8f2e" stroke-width="1.6"/><path d="M1.5 8h13M8 1.5c-3 3.5-3 9.5 0 13M8 1.5c3 3.5 3 9.5 0 13" fill="none" stroke="#5b8f2e" stroke-width="1.2"/></svg>
        www.rdb-build.com
      </li>
    </ul>
  </section>

  <section class="card card--brand" aria-label="Brand side">
    <div class="brand">
      <span class="brand__mark"></span>
      <p class="brand__name">Ridgeline<br>Design + Build</p>
    </div>
  </section>
</main>
</body>
</html>
```